Jolly Paws Business Card Update

I have a business card which I love. I want to keep the same logo, colours, font and style. I want to upgrade the scripting and remove some elements and add others.
On the front side under Services - remove the existing wording and insert - Providing individual coaching strategies to create happy, healthy and social canine companions
Under Denise Carvell amend the current wording to read: Qualified in Dog Behavioural Training, Natural Animal Healthcare and Animal Health Science
On the reverse side to remove the web address.

```html
<!DOCTYPE html>
<html lang="en">
<head>
<meta charset="utf-8">
<title>Jolly Paws Business Card</title>
<link rel="stylesheet" href="https://fonts.googleapis.com/css2?family=Montserrat:wght@400;500;700;800&display=swap">
<style>
  :root {
    --bg: #e4e4e6;
    --blue-light: #0a8ad2;
    --blue-mid: #1467c4;
    --blue-deep: #1f42a0;
    --red-bright: #e41e26;
    --red-deep: #6e0b10;
    --cream: #f4ecd2;
    --white: #ffffff;
    --ring: #c0161d;
  }
  * { box-sizing: border-box; margin: 0; padding: 0; }
  html, body { width: 1200px; height: 800px; overflow: hidden; }
  body {
    background: var(--bg);
    font-family: "Montserrat", sans-serif;
    color: var(--white);
    position: relative;
  }
  .card {
    position: absolute;
    top: 230px;
    width: 560px;
    height: 320px;
    border-radius: 26px;
    overflow: hidden;
    box-shadow: 0 14px 30px rgba(0,0,0,0.22);
  }
  .card--info { left: 30px; }
  .card--brand {
    left: 610px;
    background: linear-gradient(160deg, var(--blue-light) 0%, var(--blue-mid) 45%, var(--blue-deep) 100%);
  }

  /* info side */
  .info__top {
    position: absolute; left: 0; top: 0; width: 100%; height: 168px;
    background: linear-gradient(180deg, var(--blue-light) 0%, var(--blue-mid) 100%);
  }
  .info__band {
    position: absolute; left: 0; top: 168px; width: 100%; height: 152px;
    background: radial-gradient(ellipse at 45% 30%, var(--red-bright) 0%, #b5141a 50%, var(--red-deep) 100%);
  }
  .brand-mark {
    position: absolute; left: 40px; top: 30px;
    display: flex; flex-direction: column; align-items: center; gap: 8px;
    width: 120px;
  }
  .brand-mark__dot {
    width: 78px; height: 78px; border-radius: 50%;
    background: var(--cream);
    border: 6px solid var(--ring);
  }
  .brand-mark__name {
    font-weight: 700; font-size: 15px; letter-spacing: 0.5px; color: var(--white);
    white-space: nowrap;
  }
  .services { position: absolute; left: 200px; top: 44px; width: 340px; }
  .services__title { font-weight: 800; font-size: 21px; letter-spacing: 0.5px; margin-bottom: 8px; }
  .services__text { font-size: 14px; line-height: 1.35; font-weight: 500; white-space: nowrap; }

  .person { position: absolute; left: 34px; top: 192px; width: 290px; }
  .person__name { font-weight: 800; font-size: 22px; letter-spacing: 0.5px; margin-bottom: 8px; white-space: nowrap; }
  .person__quals { font-size: 13.5px; line-height: 1.35; font-weight: 500; white-space: nowrap; }

  .contact { position: absolute; left: 340px; top: 194px; list-style: none; }
  .contact__item {
    display: flex; align-items: center; gap: 8px;
    font-size: 13.5px; font-weight: 500; line-height: 1.5;
  }
  .contact__icon { width: 13px; height: 13px; flex: none; }

  /* brand side */
  .brand-side__dot {
    position: absolute; left: 50%; top: 48px; transform: translateX(-50%);
    width: 130px; height: 130px; border-radius: 50%;
    background: var(--cream);
    border: 8px solid var(--ring);
  }
  .brand-side__name {
    position: absolute; left: 0; width: 100%; top: 196px; text-align: center;
    font-weight: 700; font-size: 40px; letter-spacing: 2px; color: var(--white);
  }
  .brand-side__tagline {
    position: absolute; left: 0; width: 100%; top: 252px; text-align: center;
    font-weight: 500; font-size: 17px; letter-spacing: 1px; color: var(--white);
  }
</style>
</head>
<body>
  <section class="card card--info" aria-label="Business card, contact side">
    <div class="info__top"></div>
    <div class="info__band"></div>

    <div class="brand-mark">
      <div class="brand-mark__dot"></div>
      <span class="brand-mark__name">Jolly Paws</span>
    </div>

    <div class="services">
      <h2 class="services__title">SERVICES</h2>
      <p class="services__text">Providing individual coaching<br>strategies to create happy,<br>healthy &amp; social canine companions</p>
    </div>

    <div class="person">
      <h1 class="person__name">DENISE CARVELL</h1>
      <p class="person__quals">Qualified in Dog Behavioural Training<br>Natural Animal Healthcare &amp;<br>Animal Health Science</p>
    </div>

    <ul class="contact">
      <li class="contact__item">
        <svg class="contact__icon" viewBox="0 0 14 14" aria-hidden="true"><rect x="3" y="0.8" width="8" height="12.4" rx="1.5" fill="none" stroke="#fff" stroke-width="1.6"/><circle cx="7" cy="10.6" r="0.9" fill="#fff"/></svg>
        0412 708 356
      </li>
      <li class="contact__item">
        <svg class="contact__icon" viewBox="0 0 14 14" aria-hidden="true"><rect x="0.8" y="2.5" width="12.4" height="9" rx="1" fill="#fff"/><path d="M1 3 L7 8 L13 3" fill="none" stroke="#b5141a" stroke-width="1.4"/></svg>
        jollypaws1@mailbox.com
      </li>
      <li class="contact__item">
        <svg class="contact__icon" viewBox="0 0 14 14" aria-hidden="true"><circle cx="7" cy="7" r="6" fill="none" stroke="#fff" stroke-width="1.4"/><ellipse cx="7" cy="7" rx="2.6" ry="6" fill="none" stroke="#fff" stroke-width="1.1"/><path d="M1 7 H13" stroke="#fff" stroke-width="1.1"/></svg>
        jollypaws.com
      </li>
    </ul>
  </section>

  <section class="card card--brand" aria-label="Business card, brand side">
    <div class="brand-side__dot"></div>
    <p class="brand-side__name">JOLLY PAWS</p>
    <p class="brand-side__tagline">WAGGING TAILS, WARM HOMES</p>
  </section>
</body>
</html>
```